Internal web page of multinational company - Portfolio of reports

We need to improve the look & feel of an existing internal HTML page.
We use it as a portfolios where users go and see a list of existing reports as "tiles". The HTML page is automatically generated by a javascript that reads the contents to display from an HTML file.
What is needs is a "face lift" in the design of the page.
Currently we use icons on the top right of each tile to denote the type of technology used on the report and also colons for the same purpose. The attached screenshots will be self explanatory.
Across the top we have "tabs" that, once selected change the tiles.
Need a proposal for new design that keeps is as clean as possible, specially the home page that should be very light (Plimbo like).
The idea for this page is to serve as a "one stop shop" and become a bookmark for everyone in the company.
Looking for a wow effect that make is visually

Target Market(s)

Internal employees

Industry/Entity Type

It Company

Coding

Coded - Design and coding required

Number of Pages Required

2 page

Requirements
Must have
• Should not change the logo or its position from the bottom left.
• Page must be as clean as possible and
Nice to have
• Welcome to change the logo on the top left. This page is from the CSU M&I (Mni) which stands for Central Support Unit - Metrics & Insight.
Should not have
• Do no use red, this is the color of our competitor. The blue on the bottom is standard for our logo

```html
<!DOCTYPE html>
<html lang="en">
<head>
<meta charset="utf-8">
<title>CSU M&amp;I – Report Portfolio</title>
<link href="https://fonts.googleapis.com/css2?family=Arimo:wght@400;700&display=swap" rel="stylesheet">
<style>
  :root{
    --brand-blue:#0a4fa0;
    --brand-blue-dark:#003e8c;
    --brand-blue-light:#1565b8;
    --accent-blue:#0a67c2;
    --title-blue:#0b57a8;
    --text:#4a4a4a;
    --page-bg:#ececec;
    --panel-bg:#f9f9f9;
    --tile-border:#dcdcdc;
    --search-bg:#06357a;
    --help-orange:#ff8a00;
    --white:#ffffff;
  }
  *{box-sizing:border-box;margin:0;padding:0}
  html,body{width:1200px;height:871px;overflow:hidden}
  body{font-family:"Arimo",Arial,sans-serif;background:var(--page-bg);position:relative}

  .site-header{position:absolute;left:0;top:0;width:1200px;height:99px;
    background:linear-gradient(180deg,var(--brand-blue-light) 0%,var(--brand-blue-dark) 100%)}
  .site-brand{position:absolute;left:74px;top:30px;display:flex;align-items:center;gap:8px;color:var(--white)}
  .site-brand-dot{width:38px;height:38px;border-radius:50%;background:#3d8ee0}
  .site-brand-name{font-size:30px;font-weight:700;letter-spacing:0.5px}
  .search{position:absolute;left:748px;top:34px;width:324px;height:31px;border-radius:3px;
    background:var(--search-bg);display:flex;align-items:center;padding:0 10px;color:var(--white);font-size:12px}
  .search-label{flex:1}

  .portfolio{position:absolute;left:127px;top:157px;width:945px;height:569px;background:var(--panel-bg);
    box-shadow:0 3px 2px rgba(0,0,0,0.15)}

  .tile{position:absolute;width:379px;height:102px;border:1px solid var(--tile-border);border-radius:2px;
    background:linear-gradient(180deg,#ffffff 0%,#efefef 100%)}
  .tile-icon{position:absolute;left:12px;top:24px;width:52px;height:56px}
  .tile-title{position:absolute;left:82px;top:22px;font-size:20px;color:var(--title-blue);font-weight:400}
  .tile-text{position:absolute;left:82px;top:54px;width:270px;font-size:11px;line-height:15px;color:var(--text)}
  .icon-placeholder{position:absolute;left:16px;top:22px;width:44px;height:56px;border-radius:6px;
    background:linear-gradient(180deg,#2a7bd0,#0a5fb4)}

  .site-footer{position:absolute;left:0;top:779px;width:1200px;height:92px;
    background:linear-gradient(180deg,var(--brand-blue-light) 0%,var(--brand-blue-dark) 100%)}
  .help-feedback{position:absolute;left:128px;top:34px;width:125px;height:31px;border-radius:4px;
    background:var(--help-orange);color:var(--white);font-weight:700;font-size:15px;
    display:flex;align-items:center;justify-content:center}
  .help-feedback::after{content:"";position:absolute;left:68px;bottom:-12px;border-left:14px solid var(--help-orange);
    border-bottom:12px solid transparent}
  .footer-brand{position:absolute;left:962px;top:34px;color:var(--white);font-size:18px;font-weight:700}
  .footer-code{position:absolute;left:1149px;top:38px;color:var(--white);font-size:12px}
</style>
</head>
<body>
  <header class="site-header">
    <div class="site-brand"><span class="site-brand-dot"></span><span class="site-brand-name">CSU M&amp;I</span></div>
    <div class="search"><span class="search-label">Search</span>
      <svg width="12" height="12" viewBox="0 0 12 12"><circle cx="5" cy="5" r="3.6" fill="none" stroke="#fff" stroke-width="1.8"/><line x1="7.6" y1="7.6" x2="11" y2="11" stroke="#fff" stroke-width="2"/></svg>
    </div>
  </header>

  <main class="portfolio">
    <section class="tile" style="left:82px;top:67px">
      <svg class="tile-icon" viewBox="0 0 52 56">
        <g stroke="var(--accent-blue)" stroke-width="2.5" stroke-linecap="round">
          <line x1="26" y1="1" x2="26" y2="7"/><line x1="8" y1="8" x2="12" y2="12"/><line x1="44" y1="8" x2="40" y2="12"/>
          <line x1="2" y1="25" x2="7" y2="25"/><line x1="45" y1="25" x2="50" y2="25"/>
          <line x1="8" y1="42" x2="12" y2="38"/><line x1="44" y1="42" x2="40" y2="38"/>
        </g>
        <path d="M26 11a13 13 0 0 0-8 23c2 2 3 4 3 7h10c0-3 1-5 3-7a13 13 0 0 0-8-23z" fill="var(--accent-blue)"/>
        <rect x="21" y="43" width="10" height="3" rx="1" fill="var(--accent-blue)"/>
        <rect x="21" y="48" width="10" height="3" rx="1" fill="var(--accent-blue)"/>
      </svg>
      <h2 class="tile-title">Human Resources</h2>
      <p class="tile-text">Lorem Ipsum is simply dummy text of the printing and typesetting industry.</p>
    </section>

    <section class="tile" style="left:488px;top:67px">
      <div class="icon-placeholder" role="img" aria-label="Finance icon: hand holding banknotes"></div>
      <h2 class="tile-title">Finance</h2>
      <p class="tile-text">Lorem Ipsum is simply dummy text of the printing and typesetting industry.</p>
    </section>

    <section class="tile" style="left:82px;top:209px">
      <div class="icon-placeholder" role="img" aria-label="P&amp;S icon: person working at a laptop"></div>
      <h2 class="tile-title">P&amp;S</h2>
      <p class="tile-text">Lorem Ipsum is simply dummy text of the printing and typesetting industry.</p>
    </section>

    <section class="tile" style="left:488px;top:209px">
      <svg class="tile-icon" viewBox="0 0 52 56">
        <path d="M26 2 L46 10 V28 C46 40 37 49 26 54 C15 49 6 40 6 28 V10 Z" fill="var(--accent-blue)"/>
        <path d="M26 9 L40 15 V28 C40 37 34 43 26 47 C18 43 12 37 12 28 V15 Z" fill="#fff"/>
        <path d="M17 28 L24 35 L37 20" fill="none" stroke="var(--accent-blue)" stroke-width="5" stroke-linecap="round" stroke-linejoin="round"/>
      </svg>
      <h2 class="tile-title">CSU</h2>
      <p class="tile-text">Lorem Ipsum is simply dummy text of the printing and typesetting industry.</p>
    </section>

    <section class="tile" style="left:82px;top:350px">
      <svg class="tile-icon" viewBox="0 0 52 56">
        <path d="M8 18 L30 10 L46 18 V42 L24 50 L8 42 Z" fill="var(--accent-blue)"/>
        <path d="M8 18 L30 10 L46 18 L24 26 Z" fill="#2a7bd0"/>
        <g stroke="#fff" stroke-width="2" stroke-linecap="round" fill="none">
          <path d="M31 42 V32 M28 35 L31 32 L34 35"/><path d="M37 40 V30 M34 33 L37 30 L40 33"/>
        </g>
      </svg>
      <h2 class="tile-title">Distribution</h2>
      <p class="tile-text">Lorem Ipsum is simply dummy text of the printing and typesetting industry.</p>
    </section>
  </main>

  <footer class="site-footer">
    <div class="help-feedback">Help &amp; Feeback</div>
    <div class="footer-brand">Norvane</div>
    <div class="footer-code">C5</div>
  </footer>
</body>
</html>
```